Kelvara Pane Works Business Card

We need a business card design that is suitable for a Glazing Business. We Specialize in Repairing broken windows and doors and are a 24hr on call service. We manufacture Shower screens, Fly screens, Wardrobe doors, Security doors and grilles + mirrors. We stock a variety of mesh including Standard mesh, Pet resistant mesh, Tressmet & Clearweft. We would like to use a combination of Light Blue, Dark Blue, Black & White with perhaps a picture of glass breaking.

Industry/Entity Type

Business

Contact Information for Business Card

Kelvara Glass Service60B Glasshouse Rocks RdNarooma NSW 2546PH / FAX - 02 44765210MOB - 0419682350 Andrewemail - kelvarapane@fenmail.example

Font styles to use
Serif

Colors
34a7d8
0255a3
ffffff

Requirements
Must have
• logo with picture of broken or cracked glass

```html
<!DOCTYPE html>
<html lang="en">
<head>
<meta charset="utf-8">
<title>Kelvara Pane Works – Business Card</title>
<link rel="stylesheet" href="https://fonts.googleapis.com/css2?family=Questrial&family=Lato:wght@400&display=swap">
<style>
  :root {
    --backdrop: #9a9a9a;
    --card: #ffffff;
    --brand-blue: #3a55b0;
    --deep-black: #050505;
    --ink: #2b2b2b;
    --divider: #e4e4e4;
  }
  * { margin: 0; padding: 0; box-sizing: border-box; }
  html, body { width: 1200px; height: 900px; overflow: hidden; }
  body {
    background: var(--backdrop);
    position: relative;
    font-family: "Lato", sans-serif;
  }
  .card {
    position: absolute;
    top: 306px;
    width: 440px;
    height: 271px;
    background: var(--card);
    border-radius: 10px;
    overflow: hidden;
  }
  .card::before, .card::after {
    content: ""; position: absolute; left: 0; right: 0; height: 12px;
  }
  .card::before { top: 0; background: var(--brand-blue); }
  .card::after { bottom: 0; background: var(--deep-black); }
  .card--front { left: 149px; }
  .card--back { left: 608px; }

  .wordmark {
    position: absolute;
    font-family: "Questrial", sans-serif;
    color: var(--brand-blue);
    text-align: center;
    line-height: 1;
  }
  .card--front .wordmark { left: 18px; width: 186px; top: 98px; }
  .card--front .wordmark .wordmark__main { font-size: 34px; letter-spacing: 2px; display: block; }
  .card--front .wordmark .wordmark__sub { font-size: 14px; letter-spacing: 4px; display: block; margin-top: 8px; }
  .card--back .wordmark { left: 0; width: 100%; top: 62px; }
  .card--back .wordmark .wordmark__main { font-size: 76px; letter-spacing: 6px; display: block; }
  .card--back .wordmark .wordmark__sub { font-size: 24px; letter-spacing: 9px; display: block; margin-top: 14px; }

  .divider {
    position: absolute; left: 204px; top: 44px; width: 1px; height: 166px;
    background: var(--divider);
  }
  .contact-name {
    position: absolute; left: 232px; top: 84px;
    font-family: "Questrial", sans-serif; font-size: 21px; color: var(--brand-blue);
  }
  .contact-list {
    position: absolute; left: 229px; top: 124px; list-style: none;
    font-size: 12.5px; color: var(--ink);
  }
  .contact-list li { display: flex; align-items: center; height: 16px; }
  .contact-list svg { width: 9px; height: 9px; margin-right: 12px; fill: var(--brand-blue); }
  .address {
    position: absolute; left: 0; width: 100%; top: 237px;
    text-align: center; font-size: 10.5px; color: var(--ink);
    display: flex; justify-content: center; align-items: center;
  }
  .address svg { width: 8px; height: 11px; margin-right: 7px; fill: var(--brand-blue); }
  .services {
    position: absolute; left: 0; width: 100%; top: 222px;
    text-align: center; font-size: 11px; line-height: 14px; color: var(--brand-blue);
  }
</style>
</head>
<body>
  <section class="card card--front">
    <div class="wordmark">
      <span class="wordmark__main">KELVARA</span>
      <span class="wordmark__sub">Pane Works</span>
    </div>
    <div class="divider"></div>
    <p class="contact-name">Malcolm</p>
    <ul class="contact-list">
      <li><svg viewBox="0 0 10 10"><rect x="2.5" y="0" width="5" height="10" rx="1"/></svg>0419682350</li>
      <li><svg viewBox="0 0 10 10"><path d="M1 3h8v7H1z M3 0h4v3H3z"/></svg>02 48931067</li>
      <li><svg viewBox="0 0 10 10"><path d="M0 2h10v6H0z"/></svg>kelvarapane@fenmail.example</li>
    </ul>
    <p class="address"><svg viewBox="0 0 8 11"><path d="M4 0a4 4 0 0 1 4 4c0 3-4 7-4 7S0 7 0 4a4 4 0 0 1 4-4z"/></svg>17C Tindale Ridge RdKelvara NSW 2546</p>
  </section>

  <section class="card card--back">
    <div class="wordmark">
      <span class="wordmark__main">KELVARA</span>
      <span class="wordmark__sub">Pane Works</span>
    </div>
    <p class="services">Shower screens - Fly screens - Wardrobe doors -<br>Security doors and grilles + mirrors</p>
  </section>
</body>
</html>
```